Need Business Card for eLearning Company

Need a business card designed for our company, CareerVantly.

CareerVantly has developed a complete 12 lesson eLearning course to teach you the skills you need to present yourself in a job interview. The course uses advanced learning techniques in the multimedia videos, plus contains quizzes and additional exercises to insure you get the course and can walk into any interview with confidence and ease, and get the job.

www.careervantly-example.com

Industry/Entity Type

Business

```html
<!DOCTYPE html>
<html lang="en">
<head>
<meta charset="utf-8">
<title>CareerVantly Business Card</title>
<link rel="stylesheet" href="https://fonts.googleapis.com/css2?family=Mulish:wght@400;700&display=swap">
<style>
  :root {
    --bg: #1e1e1e;
    --card: #ffffff;
    --ink: #3a3a3a;
    --muted: #6a6a6a;
    --plum: #8e2a7f;
    --slate: #4a4546;
  }
  * { box-sizing: border-box; margin: 0; padding: 0; }
  html, body { width: 1200px; height: 675px; overflow: hidden; }
  body {
    background: var(--bg);
    font-family: "Mulish", sans-serif;
    display: flex;
    align-items: center;
    justify-content: center;
    gap: 40px;
  }
  .card {
    position: relative;
    width: 540px;
    height: 309px;
    background: var(--card);
    overflow: hidden;
  }
  .wordmark {
    display: flex;
    align-items: center;
    gap: 10px;
  }
  .wordmark-square {
    width: 14px; height: 14px;
    background: var(--plum);
  }
  .wordmark-name {
    font-size: 36px;
    font-weight: 400;
    color: var(--ink);
    letter-spacing: -0.5px;
    line-height: 1;
  }

  /* Front */
  .front-art {
    position: absolute;
    left: 0; top: 0;
    width: 200px; height: 309px;
    background: linear-gradient(160deg, #a34a95 0%, #9bbf3c 45%, #e9e9e9 60%, #4a4546 62%, #4a4546 100%);
  }
  .front-brand {
    position: absolute;
    right: 40px; top: 44px;
  }
  .accent-circle {
    position: absolute;
    right: -22px; top: 62px;
    width: 44px; height: 44px;
    border-radius: 50%;
    background: var(--plum);
  }
  .person {
    position: absolute;
    right: 40px; top: 112px;
    text-align: right;
  }
  .person-name { font-size: 15px; font-weight: 700; color: var(--plum); }
  .person-role { font-size: 11px; color: var(--muted); margin-top: 2px; }
  .address {
    position: absolute;
    right: 40px; top: 168px;
    text-align: right;
    font-size: 10.5px;
    line-height: 1.4;
    color: var(--muted);
  }
  .address .web { color: var(--plum); font-weight: 700; }
  .contacts {
    position: absolute;
    left: 222px; bottom: 36px;
    list-style: none;
    font-size: 10.5px;
    line-height: 1.55;
    color: var(--muted);
  }
  .contacts li { display: flex; align-items: center; gap: 7px; }
  .contacts svg { width: 10px; height: 10px; fill: var(--plum); }

  /* Back */
  .back-art {
    position: absolute;
    right: 0; top: 0;
    width: 190px; height: 309px;
    background: linear-gradient(170deg, #f1dcee 0%, #eef3dd 45%, #ececec 65%);
  }
  .back-brand {
    position: absolute;
    left: 60px; top: 98px;
  }
  .back-web {
    position: absolute;
    left: 84px; top: 196px;
    font-size: 13px;
    font-weight: 700;
    color: var(--plum);
  }
</style>
</head>
<body>
  <section class="card card-front">
    <div class="front-art" role="img" aria-label="Brand illustration area in purple, green and slate tones"></div>
    <div class="front-brand">
      <div class="wordmark"><span class="wordmark-name">careervantly</span></div>
    </div>
    <div class="accent-circle"></div>
    <div class="person">
      <div class="person-name">Daniel Okafor</div>
      <div class="person-role">Principal</div>
    </div>
    <div class="address">
      480 Harbor Lane<br>
      Springfield, IL 62701<br>
      <span class="web">www.careervantly-example.com</span>
    </div>
    <ul class="contacts">
      <li>
        <svg viewBox="0 0 10 10" aria-hidden="true"><path d="M2 1h2l1 2-1.2 1a5 5 0 0 0 2.2 2.2L7 5l2 1v2a1 1 0 0 1-1 1A7 7 0 0 1 1 2a1 1 0 0 1 1-1z"/></svg>
        555.201.4400
      </li>
      <li>
        <svg viewBox="0 0 10 10" aria-hidden="true"><rect x="1" y="2" width="8" height="7" rx="1"/><rect x="3" y="0.5" width="4" height="2" fill="#fff"/></svg>
        555.201.4411
      </li>
      <li>
        <svg viewBox="0 0 10 10" aria-hidden="true"><path d="M0.5 2h9v6h-9z"/><path d="M0.5 2l4.5 3.5L9.5 2" fill="none" stroke="#fff" stroke-width="0.8"/></svg>
        daniel@careervantly-example.com
      </li>
    </ul>
  </section>

  <section class="card card-back">
    <div class="back-art" role="img" aria-label="Faint brand illustration area in soft purple and green tones"></div>
    <div class="back-brand">
      <div class="wordmark"><span class="wordmark-square"></span><span class="wordmark-name">careervantly</span></div>
    </div>
    <div class="back-web">www.careervantly-example.com</div>
  </section>
</body>
</html>
```